Cash Balance Retirement Plan Services Page

We are looking to have a services/landing page created for one of our offerings. The goal of the page is to explain a relatively complex service (advanced retirement plan) by highlighting the benefits and uses for the plan such that it tells a story that encourages individuals and businesses that would benefit from the plans to reach out.

The page will be used both as a landing page (though secondarily) and as a page that many of our partners will show to their clients in order to generate interest. We help other people closes these deals so we want it to handle both.

Overall, we would want the page to incorporate the following sections/areas.
1. Headline and a place for a video at the top
2. Explanation of what a cash balance plan is (a paragraph or two)
3. These five benefits: These are the 7 we usually use, but only include five at a time so only need room for five.
a. Highest Tax Deductible Contributions Allowed
b. Significantly reduce your taxes
c. Potential Negative “Net Cost”
d. Owner & Executive Weighted Benefits
e. Retain and Attract Top Talen
f. Catch Up On decades of low retirement savings in a matter of years
g. Potential for life time income
4. A section comparing the contribution limits allowed for each plan type (Please see attached image as an example).
5. A place for a table of contribution amounts (This will just be an image. Also, attached).
6. A place for a compare table
6. Who should consider such a plan
7. Occasional banners for call to actions
8. FAQ

Our primary audience for this project are successful small business owners with a particular focus on medical professionals (doctors, chiropractors, dentists, plastic surgeons, etc.). In generally, they will be between 45 and 65 years old and earn $150k or more.

Because we work a lot with financial, business strategy, and insurance based products that require a significant investment by the client trust, professionalism, and sophistication are important attributes we wish to portray in the design of the page. Our preferred colors are blue or green. Though we are still working on figuring out the color scheme so your input as a designer is welcomed as your creativity can help us communicate the attributes we seek to embody for our clients.

In the attached document, I have included some additional information about the service itself if it helps to have some context, as well as a more flushed out outline of the details above.

Importantly, I am not a marketer so any creative input is always welcome if there is a best practice we are not incorporating in either our design requests or outline.

Here is the URL for our current page: https://www.brightvaleadvisors.com/physicianplan

Please don't let this page be your muse. We're trying to get away from it for a reason :) But it still will hopefully provide some helpful information, copy examples, and context.

Additionally, please don't feel like you need to read the full cash balance explanation. That's only if context will be helpful.

We are also going through a rebranding so please don't rely on the colors from the BrightValeAdvisors logo you may see on the website. I've attached two sample logos for the rebrand for context.

```html
<!DOCTYPE html>
<html lang="en">
<head>
<meta charset="utf-8">
<title>BrightVale – Cash Balance Plan</title>
<link href="https://fonts.googleapis.com/css2?family=Catamaran:wght@500;600;700;800&family=Montserrat:wght@400;500;600&family=Arimo:wght@400;700&display=swap" rel="stylesheet">
<style>
:root{
  --teal:#1aa99a;
  --teal-light:#21b9a6;
  --blue:#1b5aa8;
  --blue-dark:#163e86;
  --navy:#1726a0;
  --ink:#1d1d1f;
  --text:#333;
  --grey-bg:#eef0f3;
  --footer:#1f2226;
  --white:#fff;
}
*{box-sizing:border-box;margin:0;padding:0}
html,body{width:1200px;height:5195px;overflow:hidden}
body{font-family:"Montserrat",sans-serif;color:var(--text);background:var(--white);position:relative}
section,header,footer{position:absolute;left:0;width:1200px}
.abs{position:absolute}
.photo{position:absolute}
.btn{position:absolute;display:flex;align-items:center;justify-content:space-between;padding:0 12px 0 20px;background:var(--blue);color:#fff;font:600 11px "Montserrat",sans-serif;letter-spacing:.5px;text-transform:uppercase;border-bottom:3px solid var(--teal)}
.btn .arrow{width:28px;height:28px;border-radius:50%;background:#fff;display:flex;align-items:center;justify-content:center}
.h2{font-family:"Catamaran",sans-serif;font-weight:700;font-size:36px;color:var(--ink);text-align:center;width:1200px;left:0}
.rule{position:absolute;width:48px;height:4px;background:var(--blue);left:576px}

/* Hero */
.hero{top:0;height:666px}
.hero .photo{inset:0;background:linear-gradient(180deg,#9fb7bd 0%,#6f8d91 40%,#2f6a74 75%,#1f5058 100%)}
.nav{top:0;height:60px}
.brand{display:flex;align-items:center;gap:10px;color:#fff;font:700 25px "Catamaran",sans-serif;letter-spacing:.5px}
.brand .dot{width:34px;height:34px;border-radius:50%;border:4px solid var(--teal-light)}
.menu a{position:absolute;top:24px;color:#fff;font:500 12px "Montserrat",sans-serif;text-decoration:none}
.menu a.active{color:#bfe3ff;border-bottom:2px solid #fff;padding-bottom:8px}
.call{left:882px;top:0;width:318px;height:58px;background:var(--teal-light);display:flex;align-items:center;gap:12px;padding-left:22px;color:#fff}
.call .ico{width:32px;height:32px;border-radius:50%;background:var(--blue-dark);display:flex;align-items:center;justify-content:center}
.call small{display:block;font-size:10px}
.call b{font:600 15px "Montserrat",sans-serif}
.hero-title{top:228px;width:1200px;text-align:center;color:#fff;font:800 76px "Catamaran",sans-serif;letter-spacing:1px}
.play{left:534px;top:404px;display:flex;align-items:center;gap:10px;color:#fff;font:500 12px "Montserrat",sans-serif;text-decoration:underline}
.play .c{width:36px;height:36px;border-radius:50%;background:#fff;display:flex;align-items:center;justify-content:center}

/* What is */
.whatis{top:666px;height:538px}
.whatis h2{position:absolute;right:583px;top:72px;font:700 35px "Catamaran",sans-serif;color:var(--ink)}
.whatis .rule{left:567px;top:128px}
.whatis p{position:absolute;left:122px;top:150px;width:495px;font-size:13.5px;line-height:25.7px;text-align:justify;text-align-last:right}
.whatis .photo{left:668px;top:0;width:532px;height:538px;background:linear-gradient(160deg,#c9d6de 0%,#8fa7b5 45%,#4f6e86 100%)}

/* Benefits */
.benefits{top:1204px;height:762px}
.benefits .h2{top:68px}
.benefits .rule{top:118px}
.ben{position:absolute;width:300px;font-size:10.5px;line-height:19px;color:#555}
.ben h3{font:700 16px/24px "Catamaran",sans-serif;color:var(--ink);margin-bottom:10px}
.ben.l{text-align:right}
.ico-sq{position:absolute;width:54px;height:54px;border-radius:8px;background:linear-gradient(135deg,var(--teal-light),var(--blue));display:flex;align-items:center;justify-content:center}
.hub{position:absolute;left:478px;top:234px;width:244px;height:244px;border-radius:50%;background:#fff;box-shadow:0 6px 18px rgba(0,0,0,.18);display:flex;flex-direction:column;align-items:center;justify-content:center;gap:12px}
.hub .inner{position:absolute;inset:12px;border-radius:50%;border:3px solid var(--blue)}
.hub .dot{width:58px;height:58px;border-radius:50%;border:7px solid var(--teal)}
.hub span{font:600 27px "Catamaran",sans-serif;color:#333}

/* Limits */
.limits{top:1966px;height:878px;background:var(--teal)}
.limits .h2{top:66px;color:#fff}
.table-wrap{left:110px;top:156px;width:980px;background:#fff;padding:10px 12px 11px}
table{width:100%;border-collapse:collapse;font-family:"Arimo",sans-serif}
th{background:var(--navy);color:#fff;font:400 23px/31px "Arimo",sans-serif;text-align:left;vertical-align:top;padding:4px 8px 10px;border:1px solid #fff;height:110px}
td{background:#dbe0ee;font-size:23px;padding:8px 8px;border:1px solid #fff;height:44px;color:#111}
tr:nth-child(even) td{background:#e8ebf4}
td.b{font-weight:700}
.limits p{left:140px;top:560px;width:920px;color:#fff;font-size:13px;line-height:25.5px;text-align:center}

/* Chart */
.amounts{top:2844px;height:621px}
.amounts .h2{top:62px}
.amounts .rule{top:112px}
.bar{position:absolute}
.lbl{position:absolute;font:700 19px/22px "Arimo",sans-serif;color:#111;text-align:center}
.note{font:400 17px/22px "Arimo",sans-serif}

/* Who */
.who{top:3465px;height:660px;background:var(--grey-bg)}
.who .h2{top:70px}
.who .rule{top:120px;left:560px}
.who .frame{left:95px;top:310px;width:475px;height:282px;background:var(--blue-dark);border-radius:0 0 0 16px}
.who .photo{left:112px;top:150px;width:458px;height:430px;background:linear-gradient(135deg,#dfe8ee 0%,#b9ccd8 50%,#7f9db4 100%)}
.who .copy{left:597px;top:152px;width:493px;font-size:13.5px;line-height:25.5px;color:#333}
.who ul{list-style:none;margin-top:20px}
.who li{position:relative;padding-left:36px;margin-bottom:16px}
.who li::before{content:"";position:absolute;left:4px;top:10px;width:6px;height:6px;border-radius:50%;background:#222}

/* FAQ */
.faq{top:4125px;height:722px}
.faq .h2{top:78px}
.faq .rule{top:128px}
.q{position:absolute;left:258px;width:680px;height:44px;border:2px solid #9aa3c7;border-radius:22px;display:flex;align-items:center;gap:28px;padding-left:8px;font-size:11.5px;color:#333;box-shadow:0 2px 4px rgba(0,0,0,.15)}
.q .pm{width:26px;height:26px;border-radius:50%;border:1.5px solid var(--teal);display:flex;align-items:center;justify-content:center;color:var(--teal);font-size:16px;line-height:1}
.q.open{background:var(--teal);border-color:var(--teal);color:#fff}
.q.open .pm{border-color:#fff;color:#fff}
.answer{left:323px;top:4417px;width:530px;font-size:10.5px;line-height:19px;color:#444;position:absolute}

/* Footer */
.site-footer{top:4847px;height:348px;background:var(--footer);color:#fff}
.f-brand{left:122px;top:84px;width:150px;text-align:center;font:700 24px "Catamaran",sans-serif}
.f-brand .dot{width:64px;height:64px;border-radius:50%;border:6px solid var(--teal);margin:0 auto 10px}
.fcol{position:absolute;top:78px}
.fcol h4{font:600 18px "Catamaran",sans-serif;letter-spacing:.3px}
.fcol .u{width:40px;height:3px;background:var(--teal);margin:8px 0 14px}
.fcol a{display:block;color:#fff;font-size:10.5px;line-height:24px;text-decoration:none;text-transform:uppercase}
.soc{display:flex;gap:8px}
.soc span{width:32px;height:32px;border-radius:50%;border:1.5px solid #fff}
.copy-line{left:0;top:303px;width:1200px;text-align:center;font-size:10.5px}
.totop{left:1118px;top:240px;width:44px;height:44px;border-radius:50%;background:var(--teal);display:flex;align-items:center;justify-content:center}
</style>
</head>
<body>

<header class="hero">
  <div class="photo" role="img" aria-label="Photo of a team of smiling doctors and nurses in scrubs standing in a hospital corridor"></div>
  <div class="abs nav">
    <div class="abs brand" style="left:115px;top:16px"><span class="dot"></span>BRIGHTVALE</div>
    <nav class="menu">
      <a class="active" style="left:420px">Home</a>
      <a style="left:498px">Our Services</a>
      <a style="left:618px">About Us</a>
      <a style="left:716px">Blog</a>
      <a style="left:784px">Contact Us</a>
    </nav>
    <div class="abs call">
      <span class="ico"><svg width="14" height="14" viewBox="0 0 24 24"><path fill="#fff" d="M6.6 10.8a15 15 0 0 0 6.6 6.6l2.2-2.2c.3-.3.7-.4 1-.2 1.1.4 2.3.6 3.6.6.6 0 1 .4 1 1V20c0 .6-.4 1-1 1A17 17 0 0 1 3 4c0-.6.4-1 1-1h3.5c.6 0 1 .4 1 1 0 1.3.2 2.5.6 3.6.1.3 0 .7-.2 1z"/></svg></span>
      <div><small>Call Us</small><b>+1 (800) 555 0142</b></div>
    </div>
  </div>
  <h1 class="abs hero-title">BRIGHTVALE</h1>
  <a class="btn" style="left:508px;top:330px;width:184px;height:44px">Learn More<span class="arrow"><svg width="12" height="12" viewBox="0 0 12 12"><path d="M1 6h9M6 2l4 4-4 4" stroke="#1b5aa8" stroke-width="1.8" fill="none"/></svg></span></a>
  <div class="abs play"><span class="c"><svg width="12" height="12" viewBox="0 0 12 12"><path d="M3 1l8 5-8 5z" fill="#1b5aa8"/></svg></span>PLAY VIDEO</div>
</header>

<section class="whatis">
  <h2>What is a Cash-Balance Plan</h2>
  <div class="rule"></div>
  <p>A cash balance plan is a retirement plan specifically for small business owners, doctors, lawyers, and other high-income professionals. It allows for the highest tax-deductible contribution limits in the market, and the older you get, the higher those limits go. You then get an option for guaranteed income for life or a one time, lump payout. They are a hybrid plan that combines a the benefits of a defined benefit plan (Pensions) with those of a defined contribution plan (IRA, 401k, etc.). They are often not dependent on the stock market, which is a huge boon.</p>
  <a class="btn" style="left:432px;top:406px;width:184px;height:44px">Learn More<span class="arrow"><svg width="12" height="12" viewBox="0 0 12 12"><path d="M1 6h9M6 2l4 4-4 4" stroke="#1b5aa8" stroke-width="1.8" fill="none"/></svg></span></a>
  <div class="photo" role="img" aria-label="Photo of doctors walking down a bright hospital hallway reviewing a folder"></div>
</section>

<section class="benefits">
  <h2 class="abs h2">Our Benefits</h2>
  <div class="rule"></div>
  <svg class="abs" style="left:410px;top:166px" width="380" height="380" viewBox="0 0 380 380"><circle cx="190" cy="190" r="178" fill="none" stroke="#1b5aa8" stroke-width="1.8" stroke-dasharray="6 5"/></svg>
  <div class="hub"><div class="inner"></div><span class="dot"></span><span>BRIGHTVALE</span></div>

  <div class="ico-sq" style="left:414px;top:166px"><svg width="28" height="28" viewBox="0 0 24 24" fill="none" stroke="#fff" stroke-width="1.5"><path d="M4 20h16M7 16V9M12 16V5M17 16v-6"/></svg></div>
  <div class="ico-sq" style="left:726px;top:166px"><svg width="28" height="28" viewBox="0 0 24 24" fill="none" stroke="#fff" stroke-width="1.5"><rect x="5" y="3" width="14" height="18" rx="2"/><path d="M9 8h6M9 12h6M9 16h4"/></svg></div>
  <div class="ico-sq" style="left:414px;top:386px"><svg width="28" height="28" viewBox="0 0 24 24" fill="none" stroke="#fff" stroke-width="1.5"><path d="M3 20h18M6 17l4-5 4 3 5-7"/></svg></div>
  <div class="ico-sq" style="left:726px;top:386px"><svg width="28" height="28" viewBox="0 0 24 24" fill="none" stroke="#fff" stroke-width="1.5"><circle cx="12" cy="12" r="7"/><path d="M12 8v8M9.5 10.5h4a1.5 1.5 0 0 1 0 3h-3"/></svg></div>
  <div class="ico-sq" style="left:578px;top:480px"><svg width="28" height="28" viewBox="0 0 24 24" fill="none" stroke="#fff" stroke-width="1.5"><circle cx="8" cy="8" r="3"/><circle cx="16" cy="8" r="3"/><path d="M3 19c0-3 2-5 5-5s5 2 5 5M11 19c0-3 2-5 5-5s5 2 5 5"/></svg></div>

  <div class="ben l" style="left:100px;top:162px"><h3>Potential Negative<br>“Net Cost”</h3>Many businesses are unable to contribute to their own retirement because they also have to pay for employees. Even if they want to, the cost is often prohibitive. These plans can be designed to offer a benefit to the employee and to the business owner.</div>
  <div class="ben" style="left:798px;top:162px"><h3>Highest Tax Deductible<br>Contributions Allowed</h3>Most retirement plans in the US (IRAs, 401(k), SEP) allow $7k, $27k, or $61k a year to be contributed to retirement plans. This is a major disadvantage to individuals who have a significant income. These plans go as high as $417k.</div>
  <div class="ben l" style="left:100px;top:378px"><h3>Owner &amp; Executive<br>Weighted Benefits</h3>These plans allow greater contribution for owners and executives who are older with high income.</div>
  <div class="ben" style="left:798px;top:378px"><h3>Significantly reduce<br>your taxes</h3>Because these plans are tax-advantaged, the contributions are 100% tax deductible. That means an individual who contributes the full $417k annually will reduce their taxes by as much as $100k a year.</div>
  <div class="ben" style="left:450px;top:552px;text-align:center"><h3>Retain and Attract<br>Top Talent</h3>These plans—on top of all the benefits provided the business owners or doctors—are great for employees. Offering them helps retain and attract top talent.</div>
</section>

<section class="limits">
  <h2 class="abs h2">Comparing The Contribution Limits</h2>
  <div class="abs table-wrap">
    <table>
      <thead><tr>
        <th style="width:156px">Starting Plan at Age:</th><th style="width:160px">Max Monthly Retirement Benefit:</th><th style="width:159px">Lump Sum at Retirement:</th><th style="width:175px">Illustrative Contribution Limits:</th><th style="width:142px">Estimated Tax Savings:</th><th>“Net Cost” after Tax Savings:</th>
      </tr></thead>
      <tbody>
        <tr><td>40</td><td>$20,417</td><td>$2,959,124</td><td class="b">$141,358</td><td>$56,543</td><td>$84,814</td></tr>
        <tr><td>45</td><td>$20,417</td><td>$2,959,124</td><td class="b">$178,753</td><td>$71,501</td><td>$107,252</td></tr>
        <tr><td>50</td><td>$20,417</td><td>$2,959,124</td><td class="b">$246,962</td><td>$98,784</td><td>$148,177</td></tr>
        <tr><td>55</td><td>$20,417</td><td>$2,959,124</td><td class="b">$382,181</td><td>$152,872</td><td>$229,308</td></tr>
        <tr><td>60</td><td>$10,208</td><td>$1,479,561</td><td class="b">$400,418</td><td>$160,192</td><td>$240,225</td></tr>
      </tbody>
    </table>
  </div>
  <p class="abs">The IRS has a number of special types of retirement plans they offer people to use that come with tax-advantages. Usually, this is pre-tax contributions (also called, tax deferred). In essence, this means that the IRS encourages people to put money towards their retirement by offering them the ability to not pay taxes on what they put into retirement until later. For some individuals, this is a major advantage because they will pay higher taxes while working and lower taxes in retirement (this is not always true). Additionally, because the way the IRS taxes individuals and businesses, if they are able to shift the funds to retirement, the IRS rewards them significantly with a reduction in taxes.</p>
  <a class="btn" style="left:508px;top:746px;width:184px;height:44px">Learn More<span class="arrow"><svg width="12" height="12" viewBox="0 0 12 12"><path d="M1 6h9M6 2l4 4-4 4" stroke="#1b5aa8" stroke-width="1.8" fill="none"/></svg></span></a>
</section>

<section class="amounts">
  <h2 class="abs h2">Contribution Amounts</h2>
  <div class="rule"></div>
  <div class="lbl" style="left:128px;top:368px;width:120px">Annual Contributions Limits</div>

  <div class="lbl" style="left:258px;top:380px;width:120px">$6,000<br>($7000)</div>
  <div class="bar" style="left:278px;top:436px;width:82px;height:18px;background:#8ed35a"></div>
  <div class="lbl" style="left:258px;top:470px;width:120px">IRA</div>

  <div class="lbl" style="left:440px;top:352px;width:120px">$20,500<br>($27,000)</div>
  <div class="bar" style="left:455px;top:408px;width:82px;height:46px;background:#2ba63a"></div>
  <div class="lbl" style="left:440px;top:470px;width:120px">401(k)</div>

  <div class="lbl" style="left:612px;top:316px;width:120px">$61,000</div>
  <div class="bar" style="left:633px;top:342px;width:82px;height:112px;background:#8cbdf0"></div>
  <div class="lbl" style="left:612px;top:470px;width:120px">Profit<br>Sharin<br>g</div>

  <div class="lbl" style="left:790px;top:134px;width:120px">$416,000</div>
  <div class="bar" style="left:810px;top:158px;width:82px;height:296px;background:#1a5fd1"></div>
  <div class="lbl" style="left:790px;top:470px;width:120px">Cash<br>Balance<br>Plan</div>

  <div class="lbl note" style="left:945px;top:200px;width:120px">*Your contribution limits will be based on age and salary and may not reach the max contribution amount.</div>
</section>

<section class="who">
  <h2 class="abs h2">Who Should Consider a Cash Balance Plan?</h2>
  <div class="rule"></div>
  <div class="abs frame"></div>
  <div class="photo" role="img" aria-label="Photo of two doctors in white coats reviewing information on a tablet"></div>
  <div class="abs copy">
    <p style="text-align:justify">You should learn about your options with a Cash Balance Plan design if you are a high earning executive, partner, doctor, or successful business owner and meet the following criteria:</p>
    <ul>
      <li>You are looking to maximize your tax deductions.</li>
      <li>Your income pushes you beyond the contribution limits of the lower retirement plans such as 401(k)s, SEPs or profit sharing plans.</li>
      <li>You are in your 40s, 50s, or 60s and don’t want the “2nd best” plan.</li>
      <li>You want an option to GUARANTEE a retirement benefit.</li>
      <li>You are looking for a way to “catch-up” on retirement savings that provides massive tax savings.</li>
    </ul>
  </div>
  <a class="btn" style="left:600px;top:533px;width:184px;height:44px">Learn More<span class="arrow"><svg width="12" height="12" viewBox="0 0 12 12"><path d="M1 6h9M6 2l4 4-4 4" stroke="#1b5aa8" stroke-width="1.8" fill="none"/></svg></span></a>
</section>

<section class="faq">
  <h2 class="abs h2">FAQ</h2>
  <div class="rule"></div>
</section>
<div class="q" style="top:4288px"><span class="pm">+</span>What is your company name?</div>
<div class="q open" style="top:4352px"><span class="pm">−</span>What is your company slogan or mission statement?</div>
<p class="answer">We help our clients protect their financial futures, build generational wealth, and open doors for the highest allowable tax-deductible contributions for their retirement savings as designed by the federal government. By helping their businesses reduce their tax burden, they’re better able to provide for themselves and their employees.</p>
<div class="q" style="top:4510px"><span class="pm">+</span>Where is your company based / what areas do you operate in?</div>
<div class="q" style="top:4578px"><span class="pm">+</span>What is your goal with this content?</div>
<div class="q" style="top:4645px"><span class="pm">+</span>What are the unique selling points of your company?</div>
<a class="btn" style="left:517px;top:4715px;width:166px;height:44px">View More<span class="arrow"><svg width="12" height="12" viewBox="0 0 12 12"><path d="M1 6h9M6 2l4 4-4 4" stroke="#1b5aa8" stroke-width="1.8" fill="none"/></svg></span></a>

<footer class="site-footer">
  <div class="abs f-brand"><div class="dot"></div>BRIGHTVALE</div>
  <div class="fcol" style="left:333px"><h4>QUICK LINKS</h4><div class="u"></div><a>Home</a><a>Our Services</a><a>About Us</a><a>Portfolio</a><a>Team</a><a>Contact Us</a></div>
  <div class="fcol" style="left:520px"><h4>LINKS</h4><div class="u"></div><a>FAQ’s</a><a>Terms &amp; Conditions</a><a>Privacy Policy</a><a>Site Map</a><a>Cookies Policy</a></div>
  <div class="fcol" style="left:710px"><h4>SUPPORT</h4><div class="u"></div><a>Copyright</a><a>Legal</a><a>Privacy</a><a>Accessibility</a><a>Sitemap</a></div>
  <div class="fcol" style="left:915px"><h4>STAY CONNECTED</h4><div class="u" style="background:transparent"></div><div class="soc"><span></span><span></span><span></span></div></div>
  <div class="abs totop"><svg width="14" height="14" viewBox="0 0 14 14"><path d="M2 9l5-5 5 5" stroke="#fff" stroke-width="2" fill="none"/></svg></div>
  <div class="abs copy-line">© COPYRIGHT 2022 | ALL RIGHTS RESERVED</div>
</footer>

</body>
</html>
```